Brellwick Partners, LLC Stationary

Brellwick Partners, LLC is a new financial planning and consulting company. We are looking for designs on business cards, letterhead, envelopes, and anything else that would be useful. Our preference for business card design is two sided. We are looking for a professional and clean look with incorporating the logo and patriotic feel. Thank you to all who participate and good luck!

```html
<!DOCTYPE html>
<html lang="en">
<head>
<meta charset="utf-8">
<title>Brellwick Partners, LLC — Business Card</title>
<link href="https://fonts.googleapis.com/css2?family=Arimo:wght@400;700&display=swap" rel="stylesheet">
<style>
  :root {
    --navy: #1d3a63;
    --navy-deep: #132a4a;
    --red: #d0262f;
    --ink: #555a60;
    --paper: #ffffff;
    --stage: #ecebe8;
    --rule: #d3d5d8;
  }
  * { box-sizing: border-box; margin: 0; padding: 0; }
  html, body { width: 1200px; height: 950px; overflow: hidden; }
  body {
    background: var(--stage);
    font-family: "Arimo", Arial, sans-serif;
    position: relative;
  }
  .card {
    position: absolute;
    left: 250px;
    width: 700px;
    height: 400px;
    box-shadow: 0 6px 18px rgba(0,0,0,0.18);
  }
  /* Back side */
  .card--back {
    top: 45px;
    background: linear-gradient(135deg, var(--navy) 0%, var(--navy-deep) 100%);
    color: var(--paper);
    display: flex;
    flex-direction: column;
    align-items: center;
    justify-content: center;
  }
  .brand {
    display: flex;
    align-items: center;
    gap: 14px;
  }
  .brand__mark {
    width: 26px;
    height: 26px;
  }
  .brand__name {
    font-weight: 700;
    font-size: 34px;
    letter-spacing: 1px;
    text-transform: uppercase;
  }
  .brand__tagline {
    margin-top: 8px;
    font-size: 11px;
    letter-spacing: 2.5px;
    text-transform: uppercase;
  }
  .card--back .brand__mark { background: var(--paper); }
  .card--back .brand__name { color: var(--paper); }
  .card--back .brand__tagline { color: #c9d3e0; }
  .card--back .back__web {
    margin-top: 38px;
    font-size: 22px;
    letter-spacing: 3px;
    color: #dfe6ef;
  }
  /* Front side */
  .card--front {
    top: 505px;
    background: var(--paper);
    display: flex;
    align-items: center;
    padding: 0 40px;
  }
  .front__brand {
    width: 320px;
    display: flex;
    flex-direction: column;
    align-items: flex-start;
  }
  .card--front .brand { gap: 10px; }
  .card--front .brand__mark { width: 20px; height: 20px; background: var(--red); }
  .card--front .brand__name { font-size: 25px; color: var(--navy); letter-spacing: 0.5px; }
  .card--front .brand__tagline { font-size: 8.5px; color: var(--red); letter-spacing: 1.6px; padding-left: 30px; }
  .front__divider {
    width: 1px;
    height: 290px;
    background: var(--rule);
    margin: 0 28px 0 10px;
  }
  .front__details { color: var(--ink); }
  .person__name {
    font-weight: 700;
    font-size: 25px;
    color: var(--navy);
    letter-spacing: 0.5px;
    text-transform: uppercase;
  }
  .person__title {
    font-size: 19px;
    color: var(--red);
    text-transform: uppercase;
    margin-bottom: 16px;
  }
  .address { font-size: 18px; line-height: 24px; font-style: normal; margin-bottom: 8px; }
  .contact { list-style: none; font-size: 18px; }
  .contact li { display: flex; align-items: center; gap: 10px; line-height: 27px; }
  .contact svg { width: 16px; height: 16px; fill: var(--navy); flex: none; }
</style>
</head>
<body>
  <section class="card card--back" aria-label="Card back">
    <div class="brand">
      <span class="brand__mark"></span>
      <span class="brand__name">Brellwick Partners, LLC</span>
    </div>
    <p class="brand__tagline">Financial Planning and Consulting</p>
    <p class="back__web">www.brellwick.com</p>
  </section>

  <section class="card card--front" aria-label="Card front">
    <div class="front__brand">
      <div class="brand">
        <span class="brand__mark"></span>
        <span class="brand__name">Brellwick Partners, LLC</span>
      </div>
      <p class="brand__tagline">Financial Planning and Consulting</p>
    </div>
    <div class="front__divider"></div>
    <div class="front__details">
      <p class="person__name">Marcus Hale</p>
      <p class="person__title">President</p>
      <address class="address">2716 Larkmoor Lane<br>Ashby Grove, NY 11420</address>
      <ul class="contact">
        <li>
          <svg viewBox="0 0 16 16" aria-hidden="true"><path d="M3 1h3l1.5 4-2 1.3a9 9 0 0 0 4.2 4.2L11 8.5l4 1.5v3a2 2 0 0 1-2 2A12 12 0 0 1 1 3a2 2 0 0 1 2-2z"/></svg>
          555 0142 7781
        </li>
        <li>
          <svg viewBox="0 0 16 16" aria-hidden="true"><path d="M4 1h8v4H4z M1 6h14v6h-3v3H4v-3H1z M5 10v4h6v-4z" fill-rule="evenodd"/></svg>
          555 0187 3364
        </li>
        <li>
          <svg viewBox="0 0 16 16" aria-hidden="true"><path d="M1 3h14v10H1z M2 4l6 5 6-5" fill-rule="evenodd"/><path d="M2.5 4.5 8 9l5.5-4.5" stroke="#fff" stroke-width="1.2" fill="none"/></svg>
          marcus@brellwick.com
        </li>
        <li>
          <svg viewBox="0 0 16 16" aria-hidden="true"><circle cx="8" cy="8" r="7"/><path d="M1 8h14M8 1c-3 3.5-3 10.5 0 14M8 1c3 3.5 3 10.5 0 14" stroke="#fff" stroke-width="1" fill="none"/></svg>
          www.brellwick.com
        </li>
      </ul>
    </div>
  </section>
</body>
</html>
```